Boutique Technology Consultancy specialising is Electronic and physical security

We need to redo our existing outdated website. For your reference the link www.pelu.com.au

```html
<!DOCTYPE html>
<html lang="en">
<head>
<meta charset="utf-8">
<title>Pelu Services</title>
<link href="https://fonts.googleapis.com/css2?family=Poppins:wght@400;500;600;700&family=Playfair+Display:wght@400;500&display=swap" rel="stylesheet">
<style>
:root{
  --red:#d3201f;
  --red-dark:#8e1212;
  --black:#0b0b0b;
  --panel:#151515;
  --grey:#bdbdbd;
  --white:#ffffff;
}
*{margin:0;padding:0;box-sizing:border-box}
html,body{width:1200px;height:3900px;overflow:hidden;background:var(--black);color:var(--white);font-family:"Poppins",sans-serif}
.page{position:relative;width:1200px;height:3900px;overflow:hidden}
.abs{position:absolute}
.serif{font-family:"Playfair Display",serif}
.btn{position:absolute;background:var(--red);color:var(--white);font-size:13px;font-weight:600;text-transform:uppercase;border-radius:20px;padding:9px 28px;letter-spacing:.5px}
.section-title{position:absolute;width:100%;text-align:center;font-size:30px;font-weight:700;text-transform:uppercase}
.section-title .accent{color:var(--red)}
.title-underline{position:absolute;height:3px;width:44px;background:var(--red)}

/* top bar + nav */
.topbar{top:0;left:0;width:1200px;height:40px;background:var(--red);font-size:14px;display:flex;gap:40px;align-items:center;padding-left:110px}
.topbar span{display:flex;align-items:center;gap:8px}
.hero{top:40px;left:0;width:1200px;height:500px;background:linear-gradient(180deg,#1b2230 0%,#323a4a 45%,#1a1d24 100%)}
.nav{top:50px;left:0;width:1200px;height:60px}
.logo{position:absolute;display:flex;align-items:center;gap:10px;font-weight:700;font-size:34px;color:var(--white)}
.logo .mark{width:22px;height:22px;background:var(--red)}
.nav-links{position:absolute;top:38px;left:395px;display:flex;gap:30px;font-size:15px;font-weight:500}
.nav-links .active{border-bottom:2px solid var(--red);padding-bottom:4px}
.hero-title{top:245px;width:1200px;text-align:center;font-size:48px;line-height:58px;font-weight:700}
.hero-sub{top:372px;width:1200px;text-align:center;font-size:20px;line-height:26px}

/* about */
.about-photo{top:720px;left:60px;width:410px;height:420px;border-radius:40px;background:linear-gradient(140deg,#9fc3e6,#3f6f9e 55%,#1d3552)}
.about-list{top:985px;left:225px;width:285px;height:150px;border-radius:24px;background:var(--red);padding:22px 20px;font-size:12.5px;font-weight:500;line-height:35px;box-shadow:0 10px 30px rgba(0,0,0,.5)}
.about-list li{list-style:none;display:flex;align-items:center;gap:10px;white-space:nowrap}
.about-list svg{flex:none}
.about-title{top:735px;left:660px;font-size:32px;font-weight:700}
.about-text{left:660px;width:470px;font-size:13px;line-height:19px;text-transform:uppercase;color:#e6e6e6}

/* services */
.services{top:1180px;left:0;width:1200px;height:680px;background:linear-gradient(160deg,#3a0808,#1a0606 50%,#2a0a0a)}
.services-sub{top:1312px;width:1200px;text-align:center;font-size:26px;line-height:34px}
.card{position:absolute;top:1410px;width:240px;height:320px;background:var(--black);border:1px solid #3a3a3a;border-radius:18px;text-align:center;padding-top:24px}
.card svg{display:block;margin:0 auto 14px}
.card h3{font-family:"Playfair Display",serif;font-weight:400;font-size:22px;line-height:26px;height:56px}
.card p{font-size:17px;line-height:22px;margin-top:22px;padding:0 24px;text-align:left}
.card .btn{position:relative;display:inline-block;margin-top:16px}

/* experience */
.tile{position:absolute;top:1915px;width:200px;height:205px;background:linear-gradient(160deg,#dcdcdc,#777 55%,#2c2c2c)}
.tile span{position:absolute;left:16px;top:18px;font-size:16px;font-weight:700;line-height:20px;text-transform:uppercase}
.tile.first{background:linear-gradient(160deg,#c22626,#6a0f0f)}

/* banner */
.banner{top:2185px;left:0;width:1200px;height:380px;background:linear-gradient(100deg,#2e2e2e,#4c4c4c 50%,#1f1f1f)}
.banner-text{top:2300px;width:1200px;text-align:center;font-size:46px;line-height:56px}

/* team */
.member{position:absolute;top:2665px;width:200px;height:330px}
.member .photo{width:200px;height:205px;background:linear-gradient(180deg,#cfcfcf,#8a8a8a)}
.member .plate{margin-top:-6px;height:130px;background:var(--panel);border:1px solid #333;border-radius:0 0 14px 14px;text-align:center;padding-top:18px}
.member h4{font-size:15px;font-weight:700;text-transform:uppercase}
.member small{display:block;font-size:11px;color:var(--grey);margin-top:4px}
.social{display:flex;justify-content:center;gap:10px;margin-top:18px}
.social i{width:20px;height:20px;border-radius:50%;background:var(--red);display:block}
.arrow{position:absolute;top:2760px;width:24px;height:24px;border-radius:50%;background:var(--red)}

/* contact */
.form{top:3130px;left:300px;width:600px;height:320px;background:var(--panel);border:1px solid #333;border-radius:10px;padding:28px}
.field{position:absolute;height:34px;background:#262626;border:1px solid #3b3b3b;font-size:12px;color:#cfcfcf;padding:9px 12px}

/* footer */
.footer{top:3560px;left:0;width:1200px;height:340px;background:var(--black)}
.foot-col h5{font-size:20px;font-weight:700;text-transform:uppercase;margin-bottom:14px}
.foot-col li{list-style:none;font-size:18px;line-height:26px;display:flex;gap:8px}
.foot-col li::before{content:"›";color:var(--red)}
.contact-row{display:flex;align-items:center;gap:12px;margin-bottom:16px;font-size:12px;line-height:15px}
.contact-row i{width:24px;height:24px;border-radius:50%;background:var(--red);display:block;flex:none}
.copyright{top:3870px;width:1200px;text-align:center;font-size:11px;color:var(--grey)}
</style>
</head>
<body>
<div class="page">

  <!-- hero -->
  <div class="abs hero" role="img" aria-label="Night highway interchange with light trails"></div>
  <div class="abs topbar">
    <span><svg width="14" height="14" viewBox="0 0 24 24"><path d="M6 2l4 4-2 3c1.5 3 4 5.5 7 7l3-2 4 4-3 4C10 21 3 14 2 5z" fill="#fff"/></svg>1300 555 014</span>
    <span><svg width="16" height="12" viewBox="0 0 16 12"><rect x="0.5" y="0.5" width="15" height="11" fill="none" stroke="#fff"/><path d="M1 1l7 6 7-6" fill="none" stroke="#fff"/></svg>hello@pelu.com.au</span>
  </div>
  <div class="abs nav">
    <div class="logo" style="left:110px;top:18px"><span class="mark"></span>PELU</div>
    <div class="nav-links"><span class="active">WELCOME</span><span>EXPERIENCE</span><span>SERVICES</span><span>TEAM</span><span>ABOUT</span><span>CONTACT</span></div>
  </div>
  <h1 class="abs hero-title">YOUR TECHNOLOGY<br>PROJECTS MADE EASY</h1>
  <p class="abs hero-sub serif">Pelu is a privately owned independent consultancy<br>100% dedicated to customer satisfaction.</p>
  <span class="btn" style="top:420px;left:540px">Contact us</span>
  <svg class="abs" style="top:470px;left:0" width="1200" height="90" viewBox="0 0 1200 90">
    <path d="M0 20 Q600 90 1200 20 L1200 50 Q600 120 0 50Z" fill="var(--red-dark)"/>
    <path d="M0 30 Q600 100 1200 30 L1200 45 Q600 112 0 45Z" fill="var(--red)"/>
  </svg>

  <!-- about -->
  <div class="abs about-photo" role="img" aria-label="Glass office tower seen from below"></div>
  <ul class="abs about-list">
    <li><svg width="14" height="14" viewBox="0 0 14 14"><path d="M2 7l3 3 7-7" stroke="#fff" stroke-width="2" fill="none"/></svg>Property/Facilities Management</li>
    <li><svg width="14" height="14" viewBox="0 0 14 14"><path d="M2 7l3 3 7-7" stroke="#fff" stroke-width="2" fill="none"/></svg>Asset Management</li>
    <li><svg width="14" height="14" viewBox="0 0 14 14"><path d="M2 7l3 3 7-7" stroke="#fff" stroke-width="2" fill="none"/></svg>Development And Construction</li>
  </ul>
  <h2 class="abs about-title">ABOUT <span style="color:var(--red)">PELU</span></h2>
  <div class="title-underline" style="top:785px;left:660px"></div>
  <p class="abs about-text serif" style="top:815px">Pelu Services was established in 2006 by Ray Holden to provide technology consulting services to corporate and government clients.</p>
  <p class="abs about-text serif" style="top:890px">Pelu is a privately owned independent consultancy 100% dedicated to customer satisfaction, with experience in a range of technologies such as internet of things, security systems, BUS, building services networks, control centres and smart buildings.</p>
  <span class="btn" style="top:1035px;left:660px">Read more</span>

  <!-- services -->
  <div class="abs services" role="img" aria-label="Modern building facade in red tint"></div>
  <h2 class="section-title" style="top:1250px"><span class="accent">Our</span> Services</h2>
  <p class="abs services-sub serif">Pelu Services provides independent<br>professional services for projects</p>

  <div class="card" style="left:60px">
    <svg width="48" height="48" viewBox="0 0 48 48" fill="none" stroke="var(--red)" stroke-width="2"><circle cx="24" cy="24" r="8"/><path d="M24 4v8M24 36v8M4 24h8M36 24h8M10 10l6 6M32 32l6 6M38 10l-6 6M10 38l6-6"/></svg>
    <h3>Technology<br>Roadmaps</h3>
    <p>Lorem ipsum dolor sit amet consectetur adipiscing elit.</p>
    <span class="btn">Read more</span>
  </div>
  <div class="card" style="left:340px">
    <svg width="48" height="48" viewBox="0 0 48 48" fill="none" stroke="var(--red)" stroke-width="2"><rect x="10" y="6" width="28" height="36" rx="2"/><path d="M16 16h16M16 24h16M16 32h10"/></svg>
    <h3>Asset Management<br>Plans</h3>
    <p>Lorem ipsum dolor sit amet consectetur adipiscing elit.</p>
    <span class="btn">Read more</span>
  </div>
  <div class="card" style="left:620px">
    <svg width="48" height="48" viewBox="0 0 48 48" fill="none" stroke="var(--red)" stroke-width="2"><rect x="6" y="10" width="36" height="26" rx="2"/><path d="M16 42h16M24 36v6M14 26l8-8 6 6 8-8"/></svg>
    <h3>Project Design<br>&amp; Procurement</h3>
    <p>Lorem ipsum dolor sit amet consectetur adipiscing elit.</p>
    <span class="btn">Read more</span>
  </div>
  <div class="card" style="left:900px">
    <svg width="48" height="48" viewBox="0 0 48 48" fill="none" stroke="var(--red)" stroke-width="2"><circle cx="24" cy="16" r="8"/><path d="M8 42c2-10 8-14 16-14s14 4 16 14"/></svg>
    <h3>Operations &amp;<br>Management</h3>
    <p>Lorem ipsum dolor sit amet consectetur adipiscing elit.</p>
    <span class="btn">Read more</span>
  </div>

  <!-- experience -->
  <h2 class="section-title" style="top:1805px"><span class="accent">Our</span> Experienc</h2>
  <div class="title-underline" style="top:1850px;left:578px"></div>
  <div class="tile first" style="left:140px" role="img" aria-label="Shopping centre interior"><span>Harbour<br>Central</span></div>
  <div class="tile" style="left:380px" role="img" aria-label="City laneway with buildings"><span>Laneway</span></div>
  <div class="tile" style="left:620px" role="img" aria-label="Tall office tower"><span>Summit Towers</span></div>
  <div class="tile" style="left:860px" role="img" aria-label="Hospital building exterior"><span>St Clare Women's<br>Hospital</span></div>

  <!-- banner -->
  <div class="abs banner" role="img" aria-label="Laptop on an office desk"></div>
  <p class="abs banner-text serif">Pelu Seeks To Make The<br>World A Better Place.</p>
  <span class="btn" style="top:2440px;left:545px">Read more</span>

  <!-- team -->
  <h2 class="section-title" style="top:2585px"><span class="accent">Our</span> Team</h2>
  <div class="title-underline" style="top:2630px;left:578px"></div>
  <span class="arrow" style="left:50px"></span>
  <span class="arrow" style="left:1126px"></span>
  <div class="member" style="left:140px"><div class="photo" role="img" aria-label="Portrait of team member"></div><div class="plate"><h4>Ray Holden</h4><small>Managing Director</small><div class="social"><i></i><i></i><i></i></div></div></div>
  <div class="member" style="left:380px"><div class="photo" role="img" aria-label="Portrait of team member"></div><div class="plate"><h4>Grant Ellery</h4><small>Senior Consultant</small><div class="social"><i></i><i></i><i></i></div></div></div>
  <div class="member" style="left:620px"><div class="photo" role="img" aria-label="Portrait of team member"></div><div class="plate"><h4>Mia Corran</h4><small>Project Manager</small><div class="social"><i></i><i></i><i></i></div></div></div>
  <div class="member" style="left:860px"><div class="photo" role="img" aria-label="Portrait of team member"></div><div class="plate"><h4>Lena Vosk</h4><small>Security Engineer</small><div class="social"><i></i><i></i><i></i></div></div></div>

  <!-- contact -->
  <h2 class="section-title" style="top:3055px"><span class="accent">Contact</span> Us</h2>
  <div class="abs form"></div>
  <div class="field" style="top:3165px;left:340px;width:250px">Your Name</div>
  <div class="field" style="top:3165px;left:610px;width:250px">Your Phone</div>
  <div class="field" style="top:3215px;left:340px;width:250px">Email Address</div>
  <div class="field" style="top:3215px;left:610px;width:250px">Select Service</div>
  <div class="field" style="top:3265px;left:340px;width:520px;height:70px">Additional Message</div>
  <span class="btn" style="top:3365px;left:340px;width:520px;text-align:center;border-radius:4px">Get an appointment now</span>

  <!-- footer -->
  <svg class="abs" style="top:3480px;left:0" width="1200" height="100" viewBox="0 0 1200 100">
    <path d="M0 60 Q600 0 1200 60 L1200 100 L0 100Z" fill="var(--red-dark)"/>
    <path d="M0 75 Q600 15 1200 75 L1200 100 L0 100Z" fill="var(--red)"/>
  </svg>
  <div class="abs footer"></div>
  <div class="logo" style="left:50px;top:3625px"><span class="mark"></span>PELU</div>
  <p class="abs" style="top:3700px;left:50px;width:230px;font-size:13px;line-height:18px">Pelu is a privately owned independent consultancy 100% dedicated to customer satisfaction.</p>
  <div class="abs foot-col" style="top:3630px;left:370px"><h5>Pages</h5><ul><li>Home</li><li>About</li><li>Services</li><li>Contact</li></ul></div>
  <div class="abs foot-col" style="top:3630px;left:640px"><h5>Services</h5><ul><li>Roadmaps</li><li>Audits</li><li>Designs</li><li>Project<br>Management</li></ul></div>
  <div class="abs foot-col" style="top:3630px;left:920px"><h5>Quick Contact</h5>
    <div class="contact-row"><i></i><span>Phone<br>1300 555 014</span></div>
    <div class="contact-row"><i></i><span>Email<br>hello@pelu.com.au</span></div>
    <div class="contact-row"><i></i><span>Web<br>www.pelu.com.au</span></div>
  </div>
  <p class="abs copyright">Copyright © 2024 Pelu. All rights reserved.</p>
</div>
</body>
</html>
```